Help me make landing pages for my web application that are mobile friendly

I need to make 2 mobile friendly landing pages for an application. The 2 pages will be related. First I need a home page and then I need a working page. I do not want to change the color scheme or logos. Just layout and design.

```html
<!DOCTYPE html>
<html lang="en">
<head>
<meta charset="utf-8">
<title>Opening Details</title>
<link href="https://fonts.googleapis.com/css2?family=Poppins:wght@400;500;600;700&display=swap" rel="stylesheet">
<style>
:root{
  --ink:#2b2b2b;
  --muted:#555555;
  --field:#efefef;
  --teal:#27afcf;
  --purple:#6b4fa6;
  --red:#e5475c;
  --white:#ffffff;
  --line:#e6e6ea;
  --sky:#d6ecf4;
  --lilac:#e2def0;
}
*{box-sizing:border-box;margin:0;padding:0}
html,body{width:1200px;height:2802px;overflow:hidden}
body{
  position:relative;font-family:'Poppins',sans-serif;color:var(--ink);
  background:
    radial-gradient(ellipse 700px 600px at 1150px 120px,var(--sky),transparent 70%),
    radial-gradient(ellipse 800px 700px at 150px 2250px,var(--lilac),transparent 70%),
    radial-gradient(ellipse 600px 500px at 900px 2300px,#ecebf4,transparent 70%),
    #f7f7f9;
}
.abs{position:absolute}
.status-cover{left:0;top:0;width:893px;height:95px;background:var(--white);border-bottom-right-radius:70px}
.status-time{left:141px;top:32px;font-size:44px;font-weight:500;line-height:60px}
.status-icons{right:95px;top:48px}
.topbar-back{left:66px;top:160px;font-size:32px;font-weight:700;display:flex;align-items:center;gap:22px;letter-spacing:.3px}
.topbar-bell{left:1088px;top:155px}
.card{position:absolute;left:66px;width:1068px;background:var(--white);border:2px solid #dcdce2;border-radius:73px}
.card-title{position:absolute;left:95px;font-size:41px;font-weight:600;line-height:60px}
.toggle{position:absolute;left:931px;width:58px;height:58px;border-radius:50%;background:var(--ink);display:flex;align-items:center;justify-content:center}
.info{position:absolute;left:95px;top:172px;font-size:27px;line-height:46px}
.info-row{display:flex}
.info-label{width:388px;color:var(--ink)}
.info-value{color:var(--muted)}
.section-title{position:absolute;left:93px;font-size:40px;font-weight:600}
.field{position:absolute;left:93px;width:876px;background:var(--field);border-radius:48px}
.field-text{padding:30px 0 0 49px;font-size:33px;color:#777}
.attach{position:absolute;left:93px;width:876px;height:97px;background:var(--field);border-radius:48px;display:flex;align-items:center;padding-left:42px;gap:16px;font-size:27px}
.btn{position:absolute;height:97px;border-radius:49px;color:var(--white);font-size:29px;font-weight:600;display:flex;align-items:center;justify-content:center;gap:18px;letter-spacing:.5px}
.btn-post{left:93px;width:423px;background:var(--teal)}
.btn-upload{left:547px;width:422px;background:var(--purple)}
.field-label{position:absolute;left:95px;font-size:26px;font-weight:500}
.action{position:absolute;top:2362px;width:523px;height:123px;border-radius:62px;display:flex;align-items:center;justify-content:center;gap:16px;font-size:29px;font-weight:600;letter-spacing:.5px}
.action-save{left:66px;background:var(--purple);color:var(--white)}
.action-close{left:611px;border:3px solid var(--red);color:var(--red);background:var(--white)}
.nav{position:absolute;left:0;top:2615px;width:1200px;height:187px;background:var(--white);border-top:2px solid var(--line)}
.nav-item{position:absolute;top:40px;transform:translateX(-50%);display:flex;flex-direction:column;align-items:center;gap:18px;font-size:26px;font-weight:600;color:#8a8a8a;white-space:nowrap}
</style>
</head>
<body>
<div class="abs status-cover"></div>
<div class="abs status-time">9:41</div>
<svg class="abs status-icons" width="185" height="31" viewBox="0 0 215 36">
  <rect x="0" y="22" width="8" height="12" rx="2" fill="#111"/><rect x="12" y="16" width="8" height="18" rx="2" fill="#111"/>
  <rect x="24" y="9" width="8" height="25" rx="2" fill="#111"/><rect x="36" y="2" width="8" height="32" rx="2" fill="#111"/>
  <path d="M64 12a28 28 0 0 1 38 0l-4 4a22 22 0 0 0-30 0z M70 19a18 18 0 0 1 26 0l-4 4a12 12 0 0 0-18 0z M77 26a8 8 0 0 1 12 0l-6 7z" fill="#111"/>
  <rect x="124" y="4" width="76" height="28" rx="7" fill="none" stroke="#111" stroke-width="2.5"/>
  <rect x="129" y="9" width="66" height="18" rx="4" fill="#111"/><rect x="203" y="13" width="5" height="10" rx="2" fill="#111"/>
</svg>

<div class="abs topbar-back">
  <svg width="16" height="24" viewBox="0 0 18 26"><path d="M14 3 4 13l10 10" fill="none" stroke="#2b2b2b" stroke-width="4" stroke-linecap="round"/></svg>
  MESSAGE
</div>
<svg class="abs topbar-bell" width="48" height="58" viewBox="0 0 48 58">
  <path d="M24 8c-9 0-15 7-15 16v12l-5 7v3h40v-3l-5-7V24c0-9-6-16-15-16z" fill="#2b2b2b"/>
  <path d="M18 50a6 6 0 0 0 12 0z" fill="#2b2b2b"/>
  <circle cx="24" cy="6" r="6" fill="var(--red)"/>
</svg>

<section class="card" style="top:258px;height:1363px">
  <h2 class="card-title" style="top:70px">Opening Information</h2>
  <div class="toggle" style="top:71px"><svg width="22" height="14" viewBox="0 0 22 14"><path d="M3 3l8 8 8-8" fill="none" stroke="#fff" stroke-width="3.5" stroke-linecap="round"/></svg></div>
  <div class="info">
    <div class="info-row"><span class="info-label">Summary:</span><span class="info-value">Testing-test</span></div>
    <div class="info-row"><span class="info-label">Location:</span><span class="info-value">Demo Valley Elementary School</span></div>
    <div class="info-row"><span class="info-label">Type:</span><span class="info-value">Vacancy</span></div>
    <div class="info-row"><span class="info-label">Regular Staff:</span><span class="info-value">Nora Whitfield</span></div>
    <div class="info-row"><span class="info-label">Assignment Category:</span><span class="info-value">Teacher Department</span></div>
  </div>
  <h3 class="section-title" style="top:465px">Description</h3>
  <div class="field" style="top:548px;height:190px"><p class="field-text">Some line goes here</p></div>
  <h3 class="section-title" style="top:760px">Comments</h3>
  <div class="field" style="top:826px;height:190px"><p class="field-text">Write a comment or upload a file...</p></div>
  <div class="attach" style="top:1058px">
    <svg width="38" height="38" viewBox="0 0 24 24"><path d="M10 14a4 4 0 0 0 5.7 0l3-3a4 4 0 0 0-5.7-5.7l-1 1M14 10a4 4 0 0 0-5.7 0l-3 3a4 4 0 0 0 5.7 5.7l1-1" fill="none" stroke="#2b2b2b" stroke-width="2.2" stroke-linecap="round"/></svg>
    No comment or files uploaded
  </div>
  <div class="btn btn-post" style="top:1206px">
    <svg width="34" height="30" viewBox="0 0 24 22"><path d="M23 1 1 10l7 3 2 8 4-5 6 4z M8 13l13-10-9 12" fill="#fff"/></svg>POST
  </div>
  <div class="btn btn-upload" style="top:1206px">
    <svg width="34" height="34" viewBox="0 0 24 24"><path d="M12 16V3M6 9l6-6 6 6M3 15v5h18v-5" fill="none" stroke="#fff" stroke-width="2.2" stroke-linecap="round" stroke-linejoin="round"/></svg>UPLOAD
  </div>
</section>

<section class="card" style="top:1666px;height:386px">
  <h2 class="card-title" style="top:47px">Additional Details</h2>
  <div class="toggle" style="top:48px"><svg width="22" height="14" viewBox="0 0 22 14"><path d="M3 3l8 8 8-8" fill="none" stroke="#fff" stroke-width="3.5" stroke-linecap="round"/></svg></div>
  <p class="field-label" style="top:155px">Parking Spot</p>
  <div class="field" style="top:216px;height:97px"></div>
</section>

<section class="card" style="top:2101px;height:185px">
  <h2 class="card-title" style="top:62px">Time Slot</h2>
  <div class="toggle" style="top:63px"><svg width="14" height="22" viewBox="0 0 14 22"><path d="M3 3l8 8-8 8" fill="none" stroke="#fff" stroke-width="3.5" stroke-linecap="round"/></svg></div>
</section>

<div class="action action-save">
  <svg width="30" height="30" viewBox="0 0 24 24"><circle cx="12" cy="12" r="11" fill="#fff"/><path d="M7 12l3.5 3.5L17 9" fill="none" stroke="var(--purple)" stroke-width="3" stroke-linecap="round"/></svg>SAVE
</div>
<div class="action action-close">
  <svg width="30" height="30" viewBox="0 0 24 24"><circle cx="12" cy="12" r="11" fill="var(--red)"/><path d="M8 8l8 8M16 8l-8 8" stroke="#fff" stroke-width="3" stroke-linecap="round"/></svg>CLOSE
</div>

<nav class="nav">
  <div class="nav-item" style="left:190px">
    <svg width="56" height="56" viewBox="0 0 24 24"><path d="M3 11 12 3l9 8v10h-6v-6H9v6H3z" fill="#2b2b2b" stroke="#2b2b2b" stroke-width="1.5" stroke-linejoin="round"/></svg>HOME</div>
  <div class="nav-item" style="left:366px">
    <svg width="56" height="56" viewBox="0 0 24 24"><path d="M5 2h10l4 4v16H5z" fill="#2b2b2b"/><path d="M8 11h8M8 14h8M8 17h6" stroke="#fff" stroke-width="1.5"/></svg>OPENINGS</div>
  <div class="nav-item" style="left:582px">
    <svg width="56" height="56" viewBox="0 0 24 24"><path d="M5 2h10l4 4v16H5z" fill="#2b2b2b"/><path d="M8 11h8M8 14h8M8 17h6" stroke="#fff" stroke-width="1.5"/></svg>ASSIGNMENTS</div>
  <div class="nav-item" style="left:807px">
    <svg width="56" height="56" viewBox="0 0 24 24"><circle cx="12" cy="12" r="10.5" fill="none" stroke="#2b2b2b" stroke-width="2"/><circle cx="12" cy="9.5" r="3.5" fill="#2b2b2b"/><path d="M5.5 19a7.5 6 0 0 1 13 0" fill="#2b2b2b"/></svg>SUPPORT</div>
  <div class="nav-item" style="left:988px">
    <svg width="56" height="56" viewBox="0 0 24 24"><path d="M3 2h11v20L3 19z" fill="#2b2b2b"/><path d="M14 4h3v5M17 15v5h-3M14 12h8M19 9l3 3-3 3" fill="none" stroke="#2b2b2b" stroke-width="2" stroke-linecap="round" stroke-linejoin="round"/></svg>LOG OUT</div>
</nav>
</body>
</html>
```